English and Spanish Language School Needs a Business Card

Need a business card design a startup company called Maribel Language School. The company will offer English and Spanish conversational level courses designed to make the learner feel comfortable with grammar and vocabulary. We would like to see a logo with some colour that should communicate learning, growth.

Target Market(s)

Consumers and businesses

Industry/Entity Type

Education

Contact Information for Business Card

TBD

Font styles to use
Serif

Requirements
Must have
• Include the following
• Logo
• Name
• Title
• Cellphone Number
• Office Phone number
• Email address
• Office Address

```html
<!DOCTYPE html>
<html lang="en">
<head>
<meta charset="utf-8">
<title>Maribel Language School – Business Card</title>
<link href="https://fonts.googleapis.com/css2?family=Open+Sans:wght@400;600;700&display=swap" rel="stylesheet">
<style>
  :root {
    --backdrop-top: #262626;
    --backdrop-bottom: #050505;
    --card-white: #ffffff;
    --brand-red: #c8202a;
    --back-red: #cc1f27;
    --ink: #222222;
    --ink-soft: #333333;
  }
  * { margin: 0; padding: 0; box-sizing: border-box; }
  html, body { width: 1200px; height: 900px; overflow: hidden; }
  body {
    background: linear-gradient(to bottom, var(--backdrop-top), var(--backdrop-bottom));
    font-family: "Open Sans", Arial, sans-serif;
    position: relative;
  }
  .card {
    position: absolute;
    top: 306px;
    width: 440px;
    height: 271px;
    border-radius: 12px;
    overflow: hidden;
  }
  .card-front { left: 149px; background: var(--card-white); }
  .card-back { left: 608px; background: var(--back-red); }

  .front-brand {
    position: absolute;
    left: 228px; top: 44px;
    width: 172px;
    color: var(--brand-red);
    font-weight: 700;
    text-align: center;
    line-height: 1;
  }
  .front-brand .brand-main { display: block; font-size: 40px; letter-spacing: -1px; }
  .front-brand .brand-sub { display: block; font-size: 12px; margin-top: 2px; }

  .holder { position: absolute; left: 28px; top: 106px; }
  .holder-name { color: var(--brand-red); font-size: 15px; font-weight: 700; line-height: 18px; }
  .holder-title { color: var(--ink-soft); font-size: 12px; line-height: 16px; }

  .divider {
    position: absolute; left: 0; top: 153px;
    width: 100%; height: 3px; background: var(--brand-red);
  }

  .address {
    position: absolute; left: 28px; top: 190px;
    font-size: 12.5px; line-height: 16px; color: var(--ink);
    font-style: normal;
  }
  .contacts {
    position: absolute; right: 35px; top: 183px;
    list-style: none; font-size: 12.5px; line-height: 16px; color: var(--ink);
  }
  .contacts li { display: flex; justify-content: flex-end; align-items: center; gap: 3px; }
  .contacts svg { width: 9px; height: 9px; fill: var(--brand-red); }

  .back-brand {
    position: absolute; left: 0; right: 0; top: 90px;
    text-align: center; color: var(--card-white); font-weight: 700; line-height: 1;
  }
  .back-brand .brand-main { display: block; font-size: 64px; letter-spacing: -1px; }
  .back-brand .brand-sub { display: block; font-size: 17px; margin-top: 4px; }
</style>
</head>
<body>
  <section class="card card-front" aria-label="Business card front">
    <div class="front-brand">
      <span class="brand-main">Maribel</span>
      <span class="brand-sub">Language School</span>
    </div>
    <div class="holder">
      <p class="holder-name">Daniel Reyes</p>
      <p class="holder-title">Managing Director</p>
    </div>
    <div class="divider"></div>
    <address class="address">1234, Address GoesHere,<br>Country, 12345</address>
    <ul class="contacts">
      <li>(044) 321 654 987
        <svg viewBox="0 0 10 10"><path d="M1 3 Q5 0 9 3 L8 4.5 L6.5 3.8 L6.5 3 Q5 2.5 3.5 3 L3.5 3.8 L2 4.5 Z M2.5 5 H7.5 L8.5 9 H1.5 Z"/></svg>
      </li>
      <li>(044)987654321
        <svg viewBox="0 0 10 10"><path d="M3 0.5 H7 Q7.8 0.5 7.8 1.3 V8.7 Q7.8 9.5 7 9.5 H3 Q2.2 9.5 2.2 8.7 V1.3 Q2.2 0.5 3 0.5 Z M3.2 1.6 V7.6 H6.8 V1.6 Z"/></svg>
      </li>
      <li>info@maribelschool.com
        <svg viewBox="0 0 10 10"><path d="M0.5 2 H9.5 V8 H0.5 Z M1 2.5 L5 5.5 L9 2.5" stroke="#fff" stroke-width="0.6"/></svg>
      </li>
    </ul>
  </section>

  <section class="card card-back" aria-label="Business card back">
    <div class="back-brand">
      <span class="brand-main">Maribel</span>
      <span class="brand-sub">Language School</span>
    </div>
  </section>
</body>
</html>
```